1 Dimensional cover for digital product

Please note that if a designer comes in with an original design and other designers try to copy them too closely I will always work with the original designer in order to get the actual look I want.
Therefore it is in the interests of the designers to get their concepts in first.

I am designing some audio products for football (soccer players).

I would like a square version and a 16:9 version of the packaging completed. The square version will be for the Sonvia audio cover and the 16:9 for the thumbnails of videos.

I would like the final images in PSP files as a template that I can change the title and the main image.

I am open to creativity in this project but would like it to be a luxury and premium in what it is portraying.

I have added my logo and also the packaging that I currently use on my sister website which is not aimed at football, soccer.

I've also included an image of one of my models. This would NOT be the product image, but it could be a background image, or you may choose to leave it out altogether.

I've also included an example image as the main product image.

Although I have chosen greyscale I would also like to see products with colour.

The product page is at https://kelvarn.global/collections/all
I add this so that you can chose any one of the titles for this template

Target Market(s)

This is aimed at professional footballers

Industry/Entity Type

Sporting Good

Font styles to use
Serif
Sans Serif

Colors

Designer to choose colors to be used in the design.

Requirements
Must have
• This must look like it is made for an affluent market.
• It may also be simple in its design but I do not wish to be too prescriptive with creativity.
• My typography is Montserrat
Nice to have
• Can include the colors of my logos:
• #5BA9DE
• #272B5F
• Or you can choose to go with greyscale
Should not have
• This is a product for serious athletes so it should look very professional and adult orientated (so not cartoonish its look)

```html
<!DOCTYPE html>
<html lang="en">
<head>
<meta charset="utf-8">
<title>After Game – Hypnosis Sessions</title>
<link href="https://fonts.googleapis.com/css2?family=Montserrat:wght@400;500;600;800&display=swap" rel="stylesheet">
<style>
  :root {
    --ink: #0b0b0b;
    --band: #3a3a3a;
    --gold: #b3a66c;
    --gold-soft: #c2b57c;
    --sky: #5ba9de;
    --white: #ffffff;
    --sepia-dark: #2b2a25;
    --sepia-mid: #7d7660;
    --sepia-light: #d9d0ad;
  }
  * { margin: 0; padding: 0; box-sizing: border-box; }
  html, body { width: 1200px; height: 675px; overflow: hidden; background: var(--ink); }
  .cover {
    position: relative;
    width: 1200px;
    height: 675px;
    overflow: hidden;
    background: var(--ink);
    font-family: "Montserrat", sans-serif;
  }
  .hero-photo {
    position: absolute;
    inset: 0;
    background:
      radial-gradient(ellipse 260px 110px at 1080px 660px, rgba(255,250,225,0.85), rgba(255,250,225,0) 70%),
      radial-gradient(ellipse 420px 340px at 880px 170px, rgba(225,216,180,0.55), rgba(225,216,180,0) 75%),
      linear-gradient(90deg, rgba(11,11,11,0) 0%, rgba(11,11,11,0) 38%, var(--sepia-dark) 52%, var(--sepia-mid) 74%, var(--sepia-light) 100%);
  }
  .shapes { position: absolute; inset: 0; }
  .brand {
    position: absolute;
    left: 40px;
    top: 48px;
    width: 220px;
    text-align: center;
    color: var(--white);
  }
  .brand-dot {
    display: block;
    width: 40px;
    height: 40px;
    margin: 0 auto 12px;
    border-radius: 50%;
    background: var(--white);
  }
  .brand-name {
    font-size: 8.5px;
    font-weight: 500;
    letter-spacing: 0.3px;
  }
  .brand-line {
    display: flex;
    align-items: center;
    justify-content: center;
    gap: 6px;
    margin-top: 3px;
    font-size: 11px;
    font-weight: 400;
    letter-spacing: 0.8px;
  }
  .brand-line::before,
  .brand-line::after {
    content: "";
    width: 38px;
    height: 1px;
    background: var(--white);
  }
  .eyebrow {
    position: absolute;
    left: 202px;
    top: 226px;
    font-size: 19px;
    font-weight: 600;
    color: var(--gold-soft);
  }
  .title {
    position: absolute;
    left: 212px;
    top: 252px;
    width: 430px;
    text-align: center;
    color: var(--sky);
    font-weight: 800;
    font-size: 126px;
    line-height: 0.86;
    letter-spacing: -1px;
  }
  .tagline-mark {
    position: absolute;
    left: 134px;
    top: 514px;
    width: 34px;
    height: 34px;
    background: var(--gold);
    transform: rotate(45deg);
  }
  .tagline {
    position: absolute;
    left: 192px;
    top: 523px;
    font-size: 13.5px;
    font-weight: 400;
    color: var(--white);
    letter-spacing: 0.1px;
  }
</style>
</head>
<body>
<main class="cover">
  <div class="hero-photo" role="img" aria-label="Footballers leaping for the ball under stadium floodlights, toned in warm sepia"></div>

  <svg class="shapes" width="1200" height="675" viewBox="0 0 1200 675" aria-hidden="true">
    <defs>
      <linearGradient id="band-fade" x1="0" y1="0" x2="1" y2="0">
        <stop offset="0" stop-color="#4a4a4a" stop-opacity="0.85"/>
        <stop offset="1" stop-color="#2a2a2a" stop-opacity="0"/>
      </linearGradient>
    </defs>
    <polygon class="dark-band" points="374,0 690,0 0,675 0,374" fill="url(#band-fade)"/>
    <polygon class="gold-corner" points="0,0 374,0 0,374" fill="#b3a66c"/>
  </svg>

  <div class="brand">
    <span class="brand-dot"></span>
    <p class="brand-name">ELDRIN CASWELL HYPNOTHERAPY</p>
    <p class="brand-line">KELVARN</p>
  </div>

  <p class="eyebrow">Hypnosis sessions</p>
  <h1 class="title">AFTER<br>GAME</h1>

  <span class="tagline-mark"></span>
  <p class="tagline">CONDITIONING YOU TOWARDS EVEN BETTER FUTURE PERFORMANCES.</p>
</main>
</body>
</html>
```